Business Cards for IT Consulting Company (Managed Service Provider)

I am looking to have some business cards printed and would like some designs. We are an IT Consulting company based in Vancouver BC. I would like a nice clean and modern look to the cards. I have uploaded all the versions of my logo so parts can be used as needed. Here is a snippit from our website homepage:

Quillbrook Networks Ltd. is an IT Solutions Partner located in Vancouver BC, Canada. We offer IT solutions and support to customers in the greater Vancouver Area. With expertise in Microsoft platforms, as well as Linux and Mac OSX and over 12 years experience in the IT industry, Quillbrook Networks is dedicated to offering our clients top quality service and products. We take pride in the solutions we offer our customers. The greatest compliment a client can give us is to recommend our services.

Quillbrook Networks Ltd. offers a wide range of IT services from onsite service to remote support and managed service solutions. This allows clients to choose the support path that best suits their company’s needs. Supporting many different sized companies from small to enterprise level over the past 12 years Quillbrook Networks has the experience and expertise needed to ensure things run smoothly. Allowing our clients to focus on doing business.

Revolutionizing the way IT services are delivered.

Quillbrook Networks is dedicated to providing our clients with IT solutions that work and grow with them for years to come. This philosophy helps save money in the long run instead of replacing equipment constantly. Far too often IT solutions are not well thought out and while possibly solving the problem at hand, require replacement due to growth or quality within a very short time frame. Quillbrook Networks takes pride in providing solutions that will last and be able to accommodate growth without the need for replacement.

Industry/Entity Type

Information Technology

Contact Information for Business Card

Quillbrook Networks Ltd.
(Employee Name)
Eml: (Employees Email Address)
Web: quillbrook.me
Ph: 604-555-0148

Font styles to use
Serif
Sans Serif

Requirements
Must have
• The Company logo and company colors.
Nice to have
• - Our tag line: "Revolutionizing IT Services" or "Revolutionizing the way IT services are delivered."
• - Also I really like the idea of nature and technology together blending which is sort of where my logo came from so integrating that somehow onto the business cards would be great.

```html
<!DOCTYPE html>
<html lang="en">
<head>
<meta charset="utf-8">
<title>Quillbrook Networks Ltd. – Business Card</title>
<link rel="stylesheet" href="https://fonts.googleapis.com/css2?family=Open+Sans:wght@400;600&display=swap">
<style>
  :root {
    --backdrop: #8c8c8c;
    --card-white: #eeeff1;
    --brand-blue: #1191d2;
    --band-grey: #4b4b4d;
    --text-grey: #505052;
    --divider: #b9babc;
    --on-blue: #f2f4f6;
  }
  * { box-sizing: border-box; margin: 0; padding: 0; }
  html, body {
    width: 1105px; height: 1200px; overflow: hidden;
    background: var(--backdrop);
    font-family: "Open Sans", Arial, sans-serif;
  }
  .card {
    position: absolute; left: 182px; width: 746px; height: 426px; overflow: hidden;
  }
  .card-front { top: 120px; background: var(--card-white); }
  .card-back { top: 637px; background: var(--brand-blue); }

  .company-name {
    position: absolute; left: 66px; top: 160px;
    color: var(--brand-blue); font-weight: 600; line-height: 1;
  }
  .company-name .word { display: block; font-size: 50px; letter-spacing: -0.5px; }
  .company-name .suffix { display: block; font-size: 15px; letter-spacing: 1px; margin-top: 6px; padding-left: 4px; }

  .divider {
    position: absolute; left: 412px; top: 101px; width: 1px; height: 190px; background: var(--divider);
  }
  .contact { position: absolute; left: 447px; top: 88px; color: var(--text-grey); }
  .person-name { font-size: 30px; font-weight: 600; color: var(--brand-blue); margin-bottom: 18px; }
  .address { font-size: 19px; line-height: 28px; margin-bottom: 10px; }
  .contact-list { list-style: none; font-size: 19px; }
  .contact-list li { display: flex; align-items: center; height: 29px; }
  .contact-list svg { width: 17px; height: 17px; margin-right: 10px; fill: var(--brand-blue); flex: none; }

  .wave { position: absolute; left: 0; bottom: 0; width: 746px; height: 426px; }
  .wave .band-grey { fill: var(--band-grey); }
  .wave .band-white { fill: var(--card-white); }
  .wave .band-blue { fill: var(--brand-blue); }

  .back-name {
    position: absolute; left: 36px; top: 292px; color: var(--on-blue); font-weight: 600; line-height: 1;
  }
  .back-name .word { display: block; font-size: 50px; letter-spacing: -0.5px; }
  .back-name .suffix { display: block; font-size: 15px; letter-spacing: 1px; margin-top: 6px; padding-left: 4px; }
  .tagline { position: absolute; left: 38px; top: 370px; color: var(--on-blue); font-size: 18px; font-weight: 600; }
</style>
</head>
<body>
  <section class="card card-front">
    <div class="company-name">
      <span class="word">quillbrook</span>
      <span class="suffix">NETWORKS LTD.</span>
    </div>
    <div class="divider"></div>
    <div class="contact">
      <p class="person-name">Maren Holt</p>
      <p class="address">2140 Larchwood Road<br>Burnaby, BC V5G 0A9</p>
      <ul class="contact-list">
        <li><svg viewBox="0 0 24 24" aria-hidden="true"><path d="M6.6 10.8a15.1 15.1 0 0 0 6.6 6.6l2.2-2.2c.3-.3.7-.4 1-.2 1.1.4 2.3.6 3.6.6.6 0 1 .4 1 1V20c0 .6-.4 1-1 1A17 17 0 0 1 3 4c0-.6.4-1 1-1h3.5c.6 0 1 .4 1 1 0 1.3.2 2.5.6 3.6.1.3 0 .7-.2 1z"/></svg>604-555-0148</li>
        <li><svg viewBox="0 0 24 24" aria-hidden="true"><path d="M2 5h20v14H2z M3.5 6.5v.4l8.5 6 8.5-6v-.4z" fill-rule="evenodd"/></svg>mholt@quillbrook.me</li>
        <li><svg viewBox="0 0 24 24" aria-hidden="true"><path d="M12 2a10 10 0 1 0 0 20 10 10 0 0 0 0-20zm-1 17.9A8 8 0 0 1 4.2 10.2L9 15v1c0 1.1.9 2 2 2zm6.9-2.5A2 2 0 0 0 16 16h-1v-3c0-.6-.4-1-1-1H8v-2h2c.6 0 1-.4 1-1V7h2c1.1 0 2-.9 2-2v-.4a8 8 0 0 1 2.9 12.8z"/></svg>www.quillbrook.me</li>
      </ul>
    </div>
    <svg class="wave" viewBox="0 0 540 308" preserveAspectRatio="none" aria-hidden="true">
      <path class="band-grey" d="M0 258 C120 262 200 290 290 286 C380 281 440 262 540 261 L540 308 L0 308Z"/>
      <path class="band-white" d="M0 276 C120 279 220 296 300 292 C390 287 450 271 540 270 L540 308 L0 308Z"/>
      <path class="band-blue" d="M0 281 C120 284 220 300 300 296 C390 291 450 276 540 275 L540 308 L0 308Z"/>
    </svg>
  </section>

  <section class="card card-back">
    <div class="back-name">
      <span class="word">quillbrook</span>
      <span class="suffix">NETWORKS LTD.</span>
    </div>
    <p class="tagline">Revolutionizing IT Services</p>
  </section>
</body>
</html>
```